Brightway Haus Inc. Business Card Design

Brightway Haus Inc. is in search of a great clean design for our business cards!

Looking to incorporate our full logo and watermark on side one (however, I am open to having the text and watermark separated within the design.)

On side two, I am looking to have contact information (Name, Position, Phone #, Email, Website (www.thebrightwayhaus.ca). Can have the logo and/or watermark as part of the design if applicable.

Please add tagline "Where Shine Counts" on either side 1 or 2. This tagline can be in a sans serif, serif or cursive font as long as it compliments overall design. Capitalization can be title or sentence case depending on how it fits within the design.

Get creative!! Looking for a clean, crisp, premium design! Looking for a glossy card finish with spot UV features when printed. Cards will also be printed with rounded corners. Standard dimensions (3.5 x 2).

Target Market(s)

B2B - primary clients are business owners or property management corporations. (residential jobs are few and far between)

Industry/Entity Type

Business

Contact Information for Business Card

- clean, crisp design
- double sided
- spot UV accents and glossy finish upon printing
- standard business card size (3.5 x 2) with rounded corners
- please see project description for requirements per side

Font styles to use
Sans Serif

Requirements
Must have
• - adequate bleeds with print ready files
• - cohesive design elements between side 1 & 2
• - spot UV elements (can be on both sides or just one, use your discretion)
• - colour pallet should match the logo file provided
• - incorporate tagline "where shine counts" (this tagline can be in a serif or sans serif font as long as it is complimentary to the overall design.
Nice to have
• - Premium elements with a clean design
Should not have
• - Please omit cartoon or whimsical like designs, think premium.
• - Colours should not stray from the pallet of the provided logo.

```html
<!DOCTYPE html>
<html lang="en">
<head>
<meta charset="utf-8">
<title>Brightway Haus Inc. Business Card</title>
<link href="https://fonts.googleapis.com/css2?family=Roboto:ital,wght@0,400;0,500;0,700;0,900;1,400&display=swap" rel="stylesheet">
<style>
  :root {
    --navy: #1b2453;
    --teal: #10b6b9;
    --white: #ffffff;
    --paper: #f7f7f6;
    --grey: #b9bcbd;
    --backdrop: #e9e6e1;
  }
  html, body {
    margin: 0;
    width: 1200px;
    height: 960px;
    overflow: hidden;
    background: var(--backdrop);
    font-family: "Roboto", Arial, sans-serif;
  }
  .canvas { position: relative; width: 1200px; height: 960px; }

  .card {
    position: absolute;
    border-radius: 16px;
    overflow: hidden;
    box-shadow: 0 2px 6px rgba(0,0,0,0.18);
  }

  /* Side one */
  .card-front {
    left: 320px; top: 95px; width: 610px; height: 355px;
    background: var(--paper);
  }
  .front-wordmark {
    position: absolute; left: 0; right: 0; top: 250px;
    display: flex; justify-content: center; align-items: center; gap: 14px;
    color: var(--navy); font-weight: 900; font-size: 42px; letter-spacing: -0.5px;
    line-height: 1;
  }
  .front-wordmark .mark-square {
    width: 30px; height: 30px; background: var(--teal); flex: none;
  }
  .tagline {
    position: absolute; left: 0; right: 0; top: 288px;
    display: flex; justify-content: center; align-items: center; gap: 8px;
    font-style: italic; font-size: 18px; color: var(--navy);
  }
  .tagline .rule { width: 104px; height: 1px; background: var(--navy); }
  .tagline .accent { color: var(--teal); }

  /* Side two */
  .card-back {
    left: 320px; top: 493px; width: 600px; height: 342px;
    background: var(--navy);
    color: var(--white);
  }
  .back-wordmark {
    position: absolute; left: 28px; top: 36px;
    color: var(--teal); font-weight: 900; font-size: 30px; letter-spacing: -0.5px;
  }
  .brand-visual {
    position: absolute; right: 0; top: 0; width: 330px; height: 342px;
    background: radial-gradient(ellipse at 70% 45%, var(--teal) 0%, #48c8ca 35%, #e9f7f7 62%, rgba(27,36,83,0) 80%);
  }
  .contact { position: absolute; left: 28px; top: 118px; }
  .person-name { margin: 0; color: var(--teal); font-weight: 500; font-size: 20px; letter-spacing: 0.2px; }
  .person-role { margin: 6px 0 0; font-weight: 500; font-size: 15px; }
  .address { margin: 18px 0 0; font-size: 14px; line-height: 18px; }
  .details { list-style: none; margin: 13px 0 0; padding: 0; font-size: 14px; }
  .details li { display: flex; align-items: center; gap: 9px; height: 19px; }
  .details svg { width: 14px; height: 14px; fill: var(--teal); flex: none; }
</style>
</head>
<body>
<main class="canvas">

  <section class="card card-front" aria-label="Business card, side one">
    <div class="front-wordmark"><span class="mark-square"></span>BRIGHTWAY HAUS INC.</div>
    <p class="tagline"><span class="rule"></span><span>Where <span class="accent">Shine</span> Counts</span><span class="rule"></span></p>
  </section>

  <section class="card card-back" aria-label="Business card, side two">
    <div class="brand-visual" role="img" aria-label="Large brand emblem decoration in teal, white and grey"></div>
    <div class="back-wordmark">BRIGHTWAY HAUS INC.</div>
    <div class="contact">
      <h2 class="person-name">DANIEL MERCER</h2>
      <p class="person-role">CEO/FOUNDER</p>
      <p class="address">2140 Harbor View Road<br>Juneau, Alaska 99801</p>
      <ul class="details">
        <li><svg viewBox="0 0 16 16"><path d="M3 1h3l1.5 4-2 1.3a9 9 0 0 0 4.2 4.2L11 8.5l4 1.5v3a2 2 0 0 1-2 2A12 12 0 0 1 1 3a2 2 0 0 1 2-2z"/></svg>907 555 0142</li>
        <li><svg viewBox="0 0 16 16"><path d="M4 0h8a1 1 0 0 1 1 1v14a1 1 0 0 1-1 1H4a1 1 0 0 1-1-1V1a1 1 0 0 1 1-1zm1 2v10h6V2zm3 11a1 1 0 1 0 0 2 1 1 0 0 0 0-2z"/></svg>907 555 0187</li>
        <li><svg viewBox="0 0 16 16"><path d="M4 1h8v4H4zM1 6h14v7h-3v2H4v-2H1zm4 5v3h6v-3z"/></svg>907 555 0163</li>
        <li><svg viewBox="0 0 16 16"><path d="M1 3h14v10H1zm1.5 1.2L8 8.5l5.5-4.3z"/></svg>hello@thebrightwayhaus.ca</li>
        <li><svg viewBox="0 0 16 16"><path d="M8 1a7 7 0 1 0 0 14A7 7 0 0 0 8 1zm-1 2.2V5L5 6.5v2l2 1v2.5l1.5 1.3A5.5 5.5 0 0 1 7 3.2zm3.3 9.3L9.5 10l1.5-2.5h2a5.5 5.5 0 0 1-2.7 5z"/></svg>www.thebrightwayhaus.ca</li>
      </ul>
    </div>
  </section>

</main>
</body>
</html>
```